Business card for Luxury Portable Restroom Trailer company

We are a Luxury Portable Restroom Trailer Company Called FALCRIDGE HIRES. Based in Orange County California. We provide portable restroom trailers for events, such as, Weddings, Concerts, Charity events, Sporting events, Tournaments, Corporate events, ect. We rent and Sell the Luxury restrooms. Our colors are white, grey, and Orange. As you will see in the logo we uploaded.
There are 2 people in the company so the names and titles will change for the 3 people but card will remain the same. Here is the information for each Person: Dwight Penner CFO 555 318-0476
next Person: Leon Marchetti VP 555 318-0476
Next Person: Owen Marchetti CEO 555 318-0476
Information to include on the card: Luxury Restroom Trailers Rental and Sales. Weddings, Concerts, Charity, Sporting and Corp. Events.

```html
<!DOCTYPE html>
<html lang="en">
<head>
<meta charset="utf-8">
<title>Falcridge Hires — Business Card</title>
<link href="https://fonts.googleapis.com/css2?family=Montserrat:wght@400;500;800;900&display=swap" rel="stylesheet">
<style>
  :root {
    --orange: #f26d24;
    --white: #ffffff;
    --backdrop: #e6e6e6;
    --shadow: rgba(0, 0, 0, 0.18);
  }
  * { box-sizing: border-box; margin: 0; padding: 0; }
  html, body {
    width: 1200px; height: 880px; overflow: hidden;
    background: var(--backdrop);
    font-family: "Montserrat", sans-serif;
  }
  .canvas {
    position: relative; width: 1200px; height: 880px;
    display: flex; flex-direction: column; align-items: center; justify-content: center; gap: 40px;
  }
  .card {
    position: relative; width: 700px; height: 400px;
    background: var(--orange); color: var(--white);
    box-shadow: 0 10px 28px var(--shadow);
    overflow: hidden;
  }

  /* Front */
  .card-front { display: flex; flex-direction: column; align-items: center; }
  .brand {
    margin-top: 78px;
    display: flex; flex-direction: column; align-items: center;
    font-weight: 900; text-transform: uppercase; line-height: 1;
  }
  .brand-name { font-size: 74px; letter-spacing: 1px; }
  .brand-sub { font-size: 34px; letter-spacing: 6px; margin-top: 10px; }
  .services {
    margin-top: 58px; text-align: center;
    font-size: 19px; font-weight: 400; line-height: 1.6;
  }
  .services .dot { font-size: 14px; margin: 0 6px; vertical-align: 2px; }

  /* Back */
  .card-back .split { position: absolute; inset: 0; }
  .team {
    position: absolute; left: 56px; top: 92px;
    display: flex; flex-direction: column; gap: 14px;
  }
  .member-name { font-size: 22px; font-weight: 800; text-transform: uppercase; letter-spacing: 0.5px; }
  .member-title { font-size: 17px; font-weight: 400; margin: 3px 0 2px 18px; }
  .member-phone { display: flex; align-items: center; gap: 8px; font-size: 17px; margin-left: 18px; }
  .member-phone svg { width: 16px; height: 16px; }
  .back-brand {
    position: absolute; left: 532px; top: 120px; width: 160px;
    display: flex; flex-direction: column; align-items: center; gap: 14px;
    color: var(--orange); text-align: center;
  }
  .back-brand .disc { width: 52px; height: 52px; border-radius: 50%; background: var(--orange); }
  .back-brand .brand-text { font-size: 22px; font-weight: 800; line-height: 1.15; text-transform: uppercase; white-space: nowrap; }
</style>
</head>
<body>
<main class="canvas">
  <section class="card card-front" aria-label="Card front">
    <div class="brand">
      <span class="brand-name">Falcridge</span>
      <span class="brand-sub">Hires</span>
    </div>
    <p class="services">
      <span class="dot">●</span>Luxury Restroom Trailers Rental and Sales<br>
      <span class="dot">●</span>Weddings <span class="dot">●</span>Concerts <span class="dot">●</span>Charity <span class="dot">●</span>Sporting and Corp <span class="dot">●</span>Events
    </p>
  </section>

  <section class="card card-back" aria-label="Card back">
    <svg class="split" viewBox="0 0 700 400" preserveAspectRatio="none" aria-hidden="true">
      <polygon points="440,0 700,0 700,400 560,400" fill="var(--white)"/>
    </svg>
    <div class="team">
      <div class="member">
        <div class="member-name">Dwight Penner</div>
        <div class="member-title">CFO</div>
        <div class="member-phone">
          <svg viewBox="0 0 24 24" aria-hidden="true"><path fill="currentColor" d="M6.6 10.8a15 15 0 0 0 6.6 6.6l2.2-2.2c.3-.3.7-.4 1-.2 1.1.4 2.3.6 3.6.6.6 0 1 .4 1 1V20c0 .6-.4 1-1 1A17 17 0 0 1 3 4c0-.6.4-1 1-1h3.5c.6 0 1 .4 1 1 0 1.3.2 2.5.6 3.6.1.3 0 .7-.2 1z"/></svg>
          555 318-0476
        </div>
      </div>
      <div class="member">
        <div class="member-name">Leon Marchetti</div>
        <div class="member-title">VP</div>
        <div class="member-phone">
          <svg viewBox="0 0 24 24" aria-hidden="true"><path fill="currentColor" d="M6.6 10.8a15 15 0 0 0 6.6 6.6l2.2-2.2c.3-.3.7-.4 1-.2 1.1.4 2.3.6 3.6.6.6 0 1 .4 1 1V20c0 .6-.4 1-1 1A17 17 0 0 1 3 4c0-.6.4-1 1-1h3.5c.6 0 1 .4 1 1 0 1.3.2 2.5.6 3.6.1.3 0 .7-.2 1z"/></svg>
          555 318-0476
        </div>
      </div>
      <div class="member">
        <div class="member-name">Owen Marchetti</div>
        <div class="member-title">CEO</div>
        <div class="member-phone">
          <svg viewBox="0 0 24 24" aria-hidden="true"><path fill="currentColor" d="M6.6 10.8a15 15 0 0 0 6.6 6.6l2.2-2.2c.3-.3.7-.4 1-.2 1.1.4 2.3.6 3.6.6.6 0 1 .4 1 1V20c0 .6-.4 1-1 1A17 17 0 0 1 3 4c0-.6.4-1 1-1h3.5c.6 0 1 .4 1 1 0 1.3.2 2.5.6 3.6.1.3 0 .7-.2 1z"/></svg>
          555 318-0476
        </div>
      </div>
    </div>
    <div class="back-brand">
      <span class="disc" aria-hidden="true"></span>
      <span class="brand-text">Falcridge<br>Hires</span>
    </div>
  </section>
</main>
</body>
</html>
```